Ridgeway Mining Solutions Business Card

Ridgeway Mining Solutions is a company that provides consulting services to the Mining Industry.

Whilst Ridgeway Mining Solutions is an Australian based company its client base is the global mining industry.

The essence of Ridgeway Mining Solutions is its a can do organisation that can make a difference to its clients by providing quality assistance and form lasting relationships.
Updates

Target Market(s)

The global Mining Industry.

Industry/Entity Type

Mining

Font styles to use
Serif

Colors

Designer to choose colors to be used in the design.

Requirements
Nice to have
• My thinking is the card would look good in black given the logo.

I would like to see written on the back side of the card " Providing Metallurgical, Management and Corporate Services to the Mining Industry"

```html
<!DOCTYPE html>
<html lang="en">
<head>
<meta charset="utf-8">
<title>Ridgeway Mining Solutions — Business Card</title>
<link rel="stylesheet" href="https://fonts.googleapis.com/css2?family=Cinzel:wght@400;600&family=Tinos:wght@400;700&display=swap">
<style>
  :root {
    --ink: #0b0b0b;
    --paper: #ffffff;
    --amber: #f4a21f;
    --stone: #6b6b6b;
    --backdrop: #d9d4cc;
  }
  * { box-sizing: border-box; margin: 0; padding: 0; }
  html, body { width: 1200px; height: 870px; overflow: hidden; }
  body {
    background: var(--backdrop);
    font-family: "Tinos", "Times New Roman", serif;
    position: relative;
  }
  .card {
    position: absolute;
    top: 95px;
    width: 400px;
    height: 680px;
    box-shadow: 0 10px 30px rgba(0,0,0,0.25);
    text-align: center;
  }
  .card--front { left: 160px; background: var(--ink); color: var(--paper); }
  .card--back  { left: 640px; background: var(--paper); color: var(--stone); }

  .wordmark {
    position: absolute;
    left: 0; right: 0;
    font-family: "Tinos", "Times New Roman", serif;
    font-weight: 700;
    color: var(--amber);
    line-height: 1.05;
    letter-spacing: 2px;
  }
  .wordmark__mark {
    display: block;
    width: 14px; height: 14px;
    margin: 0 auto 14px;
    background: var(--amber);
  }
  .card--front .wordmark { top: 150px; font-size: 44px; }
  .wordmark__sub { display: block; font-size: 21px; letter-spacing: 6px; margin-top: 6px; }

  .holder { position: absolute; top: 330px; left: 0; right: 0; }
  .holder__name {
    font-family: "Cinzel", "Times New Roman", serif;
    font-size: 27px;
    letter-spacing: 1px;
  }
  .holder__role { font-size: 14px; margin-top: 2px; }

  .contacts {
    position: absolute;
    top: 470px; left: 0; right: 0;
    list-style: none;
    font-size: 18px;
    line-height: 1.75;
    letter-spacing: 0.5px;
  }

  .address-band {
    position: absolute;
    left: 0; right: 0;
    top: 598px;
    height: 44px;
    background: var(--amber);
    color: var(--ink);
    font-size: 16px;
    line-height: 44px;
    white-space: nowrap;
  }

  .card--back .wordmark { top: 250px; font-size: 40px; }
  .tagline {
    position: absolute;
    top: 420px; left: 50px; right: 50px;
    font-size: 20px;
    line-height: 1.4;
  }
</style>
</head>
<body>
  <section class="card card--front" aria-label="Card front">
    <h1 class="wordmark">
      <span class="wordmark__mark"></span>
      RIDGEWAY
      <span class="wordmark__sub">MINING SOLUTIONS</span>
    </h1>
    <div class="holder">
      <p class="holder__name">Marcus Hale</p>
      <p class="holder__role">Managing Director</p>
    </div>
    <ul class="contacts">
      <li>0098 7654 321</li>
      <li>info@ridgewaymining.com</li>
      <li>www.ridgewaymining.com</li>
    </ul>
    <p class="address-band">Ridgeway Consulting 120 Quarry Rd Perth, WA 6000</p>
  </section>

  <section class="card card--back" aria-label="Card back">
    <h2 class="wordmark">
      <span class="wordmark__mark"></span>
      RIDGEWAY
      <span class="wordmark__sub">MINING SOLUTIONS</span>
    </h2>
    <p class="tagline">Providing consulting services to the Mining Industry..</p>
  </section>
</body>
</html>
```